Podiatry clinic requires a modern revamp and editing of existing website.

I would like a fresh new look and updated information for my current business website. An easy to navigate site with prominent address and phone number for call to action. We are a podiatry clinic that focuses on general and sports podiatry.
I would like 4 pages; including Home page, About Us, Services & Contact.
www.brambleridgepodiatry.net

Target Market(s)

Active working professionals.

Industry/Entity Type

Medical

Coding

Coded - Design and coding required

Number of Pages Required

4 page

Font styles to use
Sans Serif

Colors
6b449b

Requirements
Must have
• A modern look with logo and active images; clean and uncluttered. Visible phone number and address for call to action.
• 4 pages - Home, About Us, Services, Contact.
• Home page - update address & service logos.
• About Us - update of personal information.
• Services - Revamp of existing page.
• Contact page to include Google map, email & phone number.
Nice to have
• Ability to add content easily; eg. a blog or adding video onto Home page.
• Link to Facebook page.

```html
<!DOCTYPE html>
<html lang="en">
<head>
<meta charset="utf-8">
<title>Bramble Ridge Podiatry – Contact</title>
<link rel="stylesheet" href="https://fonts.googleapis.com/css2?family=Raleway:wght@300;400;500&family=Open+Sans:wght@400;600;700&family=Roboto+Condensed:wght@300;400&display=swap">
<style>
  :root {
    --purple: #4b3397;
    --purple-brand: #6b449b;
    --purple-footer: #5a3fa3;
    --green: #7ab828;
    --grey-text: #555555;
    --body-text: #444444;
    --field-border: #c9c9c9;
    --placeholder: #8a8a8a;
    --white: #ffffff;
  }
  * { margin: 0; padding: 0; box-sizing: border-box; }
  html, body { width: 809px; height: 1200px; overflow: hidden; background: var(--white); }
  body { position: relative; font-family: "Open Sans", Arial, sans-serif; color: var(--body-text); }

  .hero {
    position: absolute; left: 0; top: 0; width: 809px; height: 456px;
    background:
      linear-gradient(90deg, rgba(110, 70, 190, 0.55) 0%, rgba(110, 70, 190, 0.1) 45%, rgba(0,0,0,0) 70%),
      linear-gradient(180deg, #eef2fb 0%, #d6dff4 30%, #b7c3ea 50%, #3d55b8 62%, #2b3fa2 80%, #3a3aa0 100%);
  }
  .hero-photo { position: absolute; inset: 0; }

  .brand {
    position: absolute; left: 52px; top: 22px;
    display: flex; align-items: center; gap: 10px;
    font-family: "Raleway", Arial, sans-serif; font-weight: 500; font-size: 22px;
    line-height: 1.15; color: var(--purple);
  }
  .brand-mark { width: 16px; height: 16px; border-radius: 50%; background: var(--purple); flex: none; }

  .quick-contact {
    position: absolute; right: 57px; top: 28px; text-align: right;
    font-family: "Roboto Condensed", Arial, sans-serif; font-weight: 300; font-size: 15px;
    color: var(--purple);
  }
  .quick-contact p { display: flex; align-items: center; justify-content: flex-end; gap: 6px; height: 22px; }
  .quick-contact p + p { margin-top: 10px; }
  .quick-contact strong { font-weight: 400; }
  .quick-contact svg { fill: var(--purple); }

  .main-nav {
    position: absolute; left: 0; top: 456px; width: 809px; height: 41px;
    background: var(--purple); display: flex; padding-left: 52px;
    font-family: "Raleway", Arial, sans-serif; font-size: 13px; color: var(--white);
  }
  .main-nav a { color: inherit; text-decoration: none; display: flex; align-items: center; height: 41px; }
  .nav-home { background: var(--green); width: 83px; justify-content: center; }
  .nav-about { margin-left: 23px; }
  .nav-services { margin-left: 50px; }
  .nav-contact { margin-left: 50px; }

  .section-title {
    position: absolute; font-family: "Raleway", Arial, sans-serif; font-weight: 300;
    font-size: 28px; color: var(--grey-text); letter-spacing: 0.2px;
  }
  .section-title span { color: var(--purple); font-weight: 400; }
  .title-contact { left: 53px; top: 545px; }
  .title-find { left: 369px; top: 545px; }
  .title-touch { left: 0; width: 809px; text-align: center; top: 836px; }

  .clinic-name {
    position: absolute; left: 53px; top: 602px;
    font-family: "Raleway", Arial, sans-serif; font-weight: 400; font-size: 21px; color: var(--purple);
  }
  .contact-list { position: absolute; left: 55px; top: 648px; list-style: none; font-size: 11px; line-height: 15.5px; }
  .contact-list li { display: flex; gap: 12px; align-items: flex-start; }
  .contact-list li + li { margin-top: 11px; }
  .contact-list svg { fill: var(--purple); flex: none; width: 14px; height: 14px; margin-top: 1px; }
  .contact-list .phone { font-weight: 700; }
  .social-link { position: absolute; left: 52px; top: 748px; width: 32px; height: 32px; border-radius: 50%; background: var(--purple); }

  .map {
    position: absolute; left: 370px; top: 604px; width: 386px; height: 196px;
    border: 1px solid var(--purple); padding: 3px; background: var(--white);
  }
  .map-area { width: 100%; height: 100%; background: linear-gradient(135deg, #f4ead6 0%, #efe3c9 50%, #f6eedd 100%); }

  .enquiry-form { position: absolute; left: 229px; top: 887px; width: 350px; }
  .field {
    width: 350px; height: 35px; border: 1px solid var(--field-border); border-radius: 3px;
    padding: 0 11px; font-family: Arial, sans-serif; font-size: 10px; color: var(--placeholder);
    display: flex; align-items: center; margin-bottom: 3.5px;
  }
  .field-message { height: 70px; align-items: flex-start; padding-top: 10px; }
  .submit {
    position: absolute; left: 119px; top: 197px; width: 112px; height: 35px; border-radius: 18px;
    background: var(--purple-brand); color: var(--white);
    font-family: "Raleway", Arial, sans-serif; font-weight: 500; font-size: 16px;
    display: flex; align-items: center; justify-content: center;
  }

  .site-footer {
    position: absolute; left: 0; top: 1165px; width: 809px; height: 35px; background: var(--purple-footer);
    color: var(--white); font-size: 11px; display: flex; align-items: center; justify-content: center;
  }
</style>
</head>
<body>
  <header class="hero">
    <div class="hero-photo" role="img" aria-label="Photo of bare feet resting on a boat railing above a blue sea"></div>
    <div class="brand"><span class="brand-mark"></span><span>Bramble Ridge<br>Podiatry</span></div>
    <div class="quick-contact">
      <p><svg width="12" height="16" viewBox="0 0 12 16"><path d="M6 0a6 6 0 0 0-6 6c0 4.5 6 10 6 10s6-5.5 6-10a6 6 0 0 0-6-6zm0 8.5A2.5 2.5 0 1 1 6 3.5a2.5 2.5 0 0 1 0 5z"/></svg>Suite 214 / 62 Harrow Lane Ashford 3100</p>
      <p><svg width="18" height="18" viewBox="0 0 24 24"><path d="M6.6 10.8a15.1 15.1 0 0 0 6.6 6.6l2.2-2.2a1 1 0 0 1 1-.25 11.4 11.4 0 0 0 3.6.57 1 1 0 0 1 1 1V20a1 1 0 0 1-1 1A17 17 0 0 1 3 4a1 1 0 0 1 1-1h3.5a1 1 0 0 1 1 1c0 1.25.2 2.45.57 3.57a1 1 0 0 1-.25 1z"/></svg>CALL US NOW : <strong>1300 555 018</strong></p>
    </div>
  </header>

  <nav class="main-nav">
    <a class="nav-home" href="#">HOME</a>
    <a class="nav-about" href="#">ABOUT</a>
    <a class="nav-services" href="#">SERVICES</a>
    <a class="nav-contact" href="#">CONTACT</a>
  </nav>

  <h1 class="section-title title-contact">CONTACT <span>US</span></h1>
  <h2 class="section-title title-find">FIND <span>US</span></h2>

  <h3 class="clinic-name">BRAMBLE RIDGE PODIATRY</h3>
  <ul class="contact-list">
    <li><svg viewBox="0 0 12 16"><path d="M6 0a6 6 0 0 0-6 6c0 4.5 6 10 6 10s6-5.5 6-10a6 6 0 0 0-6-6zm0 8.5A2.5 2.5 0 1 1 6 3.5a2.5 2.5 0 0 1 0 5z"/></svg><span>Suite 214 / 62 Harrow Lane<br>Ashford 3100.</span></li>
    <li class="phone"><svg viewBox="0 0 24 24"><path d="M6.6 10.8a15.1 15.1 0 0 0 6.6 6.6l2.2-2.2a1 1 0 0 1 1-.25 11.4 11.4 0 0 0 3.6.57 1 1 0 0 1 1 1V20a1 1 0 0 1-1 1A17 17 0 0 1 3 4a1 1 0 0 1 1-1h3.5a1 1 0 0 1 1 1c0 1.25.2 2.45.57 3.57a1 1 0 0 1-.25 1z"/></svg><span>1300 555 018</span></li>
    <li><svg viewBox="0 0 24 24"><path d="M2 5h20v14H2zm2 2v.4l8 5.2 8-5.2V7zm16 2.8-8 5.2-8-5.2V17h16z"/></svg><span>info@brambleridgepodiatry.net</span></li>
  </ul>
  <a class="social-link" href="#" aria-label="Social page"></a>

  <div class="map"><div class="map-area" role="img" aria-label="Street map showing the clinic location"></div></div>

  <h2 class="section-title title-touch">GET IN <span>TOUCH WITH US</span></h2>
  <form class="enquiry-form">
    <div class="field">Name</div>
    <div class="field">E-Mail</div>
    <div class="field">Phone</div>
    <div class="field field-message">Message</div>
    <div class="submit">SUBMIT</div>
  </form>

  <footer class="site-footer">© Bramble Ridge Podiatry- 2016. All Rights Reserved.</footer>
</body>
</html>
```